Building company buisness cards

We are looking for a sharp modern new look for our business cards.We are a New Zealand based company that specialises in house and land packages.We have attached a photo of the current logo and would like to see if it can be improved somehow if needed.We are open to any colours but we have chosen Black and White at this stage. Feel free to change the font and make the logo smarter looking.Play with the colours and see what looks best.We want a card that looks so good know one will want to throw it away!

Target Market(s)

Building profesonals, home buyers

Industry/Entity Type

Building

Contact Information for Business Card

Garrick Tenwood
0275390628
garrickt@hartvale.co.nz

Font styles to use
Serif
Sans Serif

Colors

Designer to choose colors to be used in the design.

Requirements
Must have
• Just the logo on one side and details on the other
• Clean simple looking card
Nice to have
• Round corners and detail like raised or spot UV
• Something that stands out
Should not have
• To title needed, Director etc

```html
<!DOCTYPE html>
<html lang="en">
<head>
<meta charset="utf-8">
<title>Hartvale Business Cards</title>
<link rel="stylesheet" href="https://fonts.googleapis.com/css2?family=Playfair+Display:wght@700;900&family=Lato:wght@400&display=swap">
<style>
  :root {
    --backdrop: #5e5e5e;
    --card-black: #0b0c10;
    --panel-grey: #a3a3a3;
    --band-white: #f4f3ee;
    --ink-white: #ffffff;
  }
  * { margin: 0; padding: 0; box-sizing: border-box; }
  html, body { width: 1200px; height: 802px; overflow: hidden; }
  body { background: var(--backdrop); position: relative; }

  .card {
    position: absolute;
    top: 274px;
    width: 440px;
    height: 262px;
    border-radius: 15px;
    background: var(--card-black);
    overflow: hidden;
    box-shadow: 0 4px 10px rgba(0,0,0,0.45);
  }
  .card--details { left: 136px; }
  .card--brand { left: 627px; }

  .card__accent { position: absolute; left: 0; top: 0; width: 440px; height: 262px; }

  .wordmark {
    color: var(--ink-white);
    font-family: "Playfair Display", Georgia, serif;
    font-weight: 900;
    line-height: 1;
    white-space: nowrap;
  }
  .card--details .wordmark {
    position: absolute;
    right: 24px;
    top: 82px;
    font-size: 40px;
  }

  .contact {
    position: absolute;
    right: 21px;
    top: 150px;
    text-align: right;
    color: var(--ink-white);
  }
  .contact__name {
    font-family: "Playfair Display", Georgia, serif;
    font-weight: 700;
    font-size: 21px;
    margin-bottom: 14px;
  }
  .contact__line {
    font-family: "Lato", Arial, sans-serif;
    font-size: 13px;
    line-height: 18px;
    display: flex;
    justify-content: flex-end;
    align-items: center;
    gap: 4px;
  }
  .contact__icon { width: 12px; height: 12px; fill: var(--ink-white); }

  .brand-lockup {
    position: absolute;
    left: 0;
    right: 0;
    top: 100px;
    display: flex;
    flex-direction: column;
    align-items: center;
  }
  .brand-lockup__inner { display: inline-block; }
  .card--brand .wordmark { font-size: 54px; }
  .brand-lockup__tagline {
    font-family: "Lato", Arial, sans-serif;
    font-size: 11.5px;
    color: var(--ink-white);
    margin-top: 2px;
    margin-left: 2px;
  }
</style>
</head>
<body>
  <section class="card card--details">
    <svg class="card__accent" viewBox="0 0 440 262" aria-hidden="true">
      <polygon points="0,0 177,0 27,262 0,262" fill="var(--panel-grey)"/>
      <polygon points="177,0 226,0 55,262 27,262" fill="var(--band-white)"/>
    </svg>
    <div class="wordmark">Hartvale</div>
    <div class="contact">
      <p class="contact__name">Garrick Tenwood</p>
      <p class="contact__line">0275390628
        <svg class="contact__icon" viewBox="0 0 24 24" aria-hidden="true"><path d="M3 8c0-3 4-5 9-5s9 2 9 5v2h-5V8c-1-1-3-1-4-1s-3 0-4 1v2H3zm4 4h10l3 8H4z"/></svg>
      </p>
      <p class="contact__line">garrickt@hartvale.co.nz
        <svg class="contact__icon" viewBox="0 0 24 24" aria-hidden="true"><path d="M2 5h20v14H2zm2 2v1l8 5 8-5V7l-8 5z"/></svg>
      </p>
    </div>
  </section>

  <section class="card card--brand">
    <div class="brand-lockup">
      <div class="brand-lockup__inner">
        <div class="wordmark">Hartvale</div>
        <p class="brand-lockup__tagline">Homes shaped around you.</p>
      </div>
    </div>
  </section>
</body>
</html>
```